Business Card Design

We are a company that provides stump grinding services for residential and commercial clients. Looking for a simple business card design that may have some type of graphic on the card that will tie in with the Tamsen name(Grizzly Bear, Paw Print, etc) . Possibly some foliage wrapping around part of the card? Would like to have a simple design that stands out because it is unique. We are working on getting the website set up and there is a simple graphic on the top of the page that came to mind when I mentioned the leaves.

Industry/Entity Type

Business

Contact Information for Business Card

Tamsen Stump Grinding 303-257-4788KodiakStumps.Com

Font styles to use
Serif

Requirements
Must have
• Business name
• Website Address
• Phone Number
Nice to have
• Graphics that would be associated with a Tamsen bear.
Should not have
• Nothing frilly

```html
<!DOCTYPE html>
<html lang="en">
<head>
<meta charset="utf-8">
<title>Tamsen Stump Grinding – Business Card</title>
<link rel="stylesheet" href="https://fonts.googleapis.com/css2?family=Cinzel:wght@400&family=Open+Sans:wght@400&display=swap">
<style>
  :root {
    --backdrop: #a3a3a3;
    --card: #000000;
    --ink: #ffffff;
    --rule: #5a5a5a;
    --mark-line: #8c8c8c;
  }
  * { margin: 0; padding: 0; box-sizing: border-box; }
  html, body { width: 1200px; height: 900px; overflow: hidden; }
  body { background: var(--backdrop); position: relative; }

  .card {
    position: absolute;
    top: 275px;
    width: 477px;
    height: 294px;
    background: var(--card);
    color: var(--ink);
  }
  .card--front { left: 116px; border-radius: 0 56px 0 56px; }
  .card--back  { left: 622px; border-radius: 56px 0 56px 0; }

  .brand-lockup {
    position: absolute;
    left: 44px;
    top: 54px;
    display: flex;
    align-items: center;
  }
  .brand-circle {
    width: 74px;
    height: 74px;
    border: 2px solid var(--mark-line);
    border-radius: 50%;
  }
  .brand-divider {
    width: 1px;
    height: 70px;
    background: var(--rule);
    margin: 0 18px 0 70px;
  }
  .brand-name {
    font-family: "Cinzel", serif;
    font-weight: 400;
    color: var(--ink);
    line-height: 1.1;
  }
  .brand-name__top { display: block; font-size: 24px; letter-spacing: 0.5px; }
  .brand-name__bottom { display: block; font-size: 20px; letter-spacing: 7px; }

  .contact {
    position: absolute;
    left: 0;
    right: 0;
    top: 205px;
    list-style: none;
    text-align: center;
    font-family: "Open Sans", sans-serif;
    font-size: 13px;
    line-height: 20px;
    color: var(--ink);
  }
  .contact__item { display: flex; justify-content: center; align-items: center; gap: 6px; }
  .contact__icon { width: 11px; height: 11px; }

  .back-name {
    position: absolute;
    left: 0;
    right: 0;
    top: 106px;
    text-align: center;
    font-family: "Cinzel", serif;
    font-weight: 400;
    color: var(--ink);
    line-height: 1.2;
  }
  .back-name__top { display: block; font-size: 36px; letter-spacing: 1px; }
  .back-name__bottom { display: block; font-size: 32px; letter-spacing: 14px; margin-left: 14px; }
</style>
</head>
<body>
  <section class="card card--front" aria-label="Business card front">
    <div class="brand-lockup">
      <div class="brand-circle" aria-hidden="true"></div>
      <div class="brand-divider" aria-hidden="true"></div>
      <p class="brand-name">
        <span class="brand-name__top">Tamsen Stump</span>
        <span class="brand-name__bottom">Grinding</span>
      </p>
    </div>
    <ul class="contact">
      <li class="contact__item">
        <svg class="contact__icon" viewBox="0 0 12 12" aria-hidden="true">
          <path d="M1 4 Q6 0 11 4 L9.5 5.5 L8 4.5 L8 3.5 Q6 3 4 3.5 L4 4.5 L2.5 5.5 Z" fill="#fff"/>
          <rect x="2.5" y="6" width="7" height="5" rx="1" fill="#fff"/>
        </svg>
        <span>303-555-0146</span>
      </li>
      <li class="contact__item">
        <svg class="contact__icon" viewBox="0 0 12 12" aria-hidden="true" fill="none" stroke="#fff" stroke-width="1.3">
          <rect x="0.8" y="5" width="6" height="3" rx="1.5" transform="rotate(-45 3.8 6.5)"/>
          <rect x="5.2" y="4" width="6" height="3" rx="1.5" transform="rotate(-45 8.2 5.5)"/>
        </svg>
        <span>TamsenStumps.Com</span>
      </li>
    </ul>
  </section>

  <section class="card card--back" aria-label="Business card back">
    <p class="back-name">
      <span class="back-name__top">Tamsen Stump</span>
      <span class="back-name__bottom">Grinding</span>
    </p>
  </section>
</body>
</html>
```